Unique Business Card Design

Unique Business Card design for our orthotic and prosthetic company. Our logo is on our website, color is light blue. Unique shape (artificial leg shaped, vertical, etc..) preferred. Logo, business name, individual name and basic demographics needed.

Industry/Entity Type

Business

Contact Information for Business Card

Logo, Industry, Phone # Logo, "Prosthetic & Orthotic Services" Place to add individual name and contact info

Colors
cee9f5

Requirements
Must have
• The icon must be there, placement of "Prosthetic & Orthotic Services" can be moved
Nice to have
• Like the mix of light blue, and a little darker blue. One design included the icons from my website which was a nice touch

```html
<!DOCTYPE html>
<html lang="en">
<head>
<meta charset="utf-8">
<title>Limbworks Inc. – Business Card</title>
<link href="https://fonts.googleapis.com/css2?family=Montserrat:wght@400;500;600;700&family=Petit+Formal+Script&display=swap" rel="stylesheet">
<style>
  :root {
    --brand-blue: #1a62b0;
    --brand-blue-deep: #15509a;
    --brand-light: #cee9f5;
    --ink: #1c1c1c;
    --paper: #ffffff;
    --stage: #e6eaee;
  }
  * { box-sizing: border-box; margin: 0; padding: 0; }
  html, body {
    width: 1200px; height: 900px; overflow: hidden;
    background: var(--stage);
    font-family: "Montserrat", Arial, sans-serif;
  }
  .sheet {
    width: 1200px; height: 900px;
    display: flex; align-items: center; justify-content: center; gap: 40px;
  }
  .card {
    position: relative;
    width: 540px; height: 310px;
    border-radius: 22px;
    box-shadow: 0 10px 28px rgba(0,0,0,.18);
    overflow: hidden;
  }

  /* Front */
  .card--front { background: var(--brand-blue); color: var(--paper); }
  .front__badge {
    position: absolute; left: 44px; top: 62px;
    width: 118px; height: 118px; border-radius: 50%;
    background: var(--paper);
  }
  .front__brand {
    position: absolute; left: 182px; top: 66px;
  }
  .brand-name {
    font-weight: 600; font-size: 33px; letter-spacing: .5px;
    color: var(--paper); line-height: 1;
    padding-bottom: 7px;
    border-bottom: 3px solid var(--paper);
  }
  .brand-tagline {
    font-family: "Petit Formal Script", "Times New Roman", serif;
    font-size: 16px; margin-top: 8px; margin-left: 40px;
    color: var(--paper);
  }
  .services {
    position: absolute; left: 190px; right: 30px; top: 190px;
    display: flex; justify-content: space-between;
    list-style: none;
  }
  .service {
    display: flex; flex-direction: column; align-items: center; gap: 10px;
    width: 110px;
  }
  .service__icon {
    width: 48px; height: 48px; border-radius: 50%;
    background: radial-gradient(circle at 35% 30%, #ffffff 0%, var(--brand-light) 45%, #8fbfe3 100%);
    box-shadow: 0 2px 4px rgba(0,0,0,.25);
  }
  .service__label {
    font-size: 13px; font-weight: 600; letter-spacing: .3px;
  }

  /* Back */
  .card--back { background: var(--paper); color: var(--ink); }
  .back__badge {
    position: absolute; left: 34px; top: 58px;
    width: 194px; height: 194px; border-radius: 50%;
    background: var(--brand-blue);
    display: flex; align-items: center; justify-content: center;
  }
  .back__badge-name {
    font-weight: 600; font-size: 19px; color: var(--paper);
    text-align: center; line-height: 1.25;
  }
  .back__divider {
    position: absolute; left: 258px; top: 60px;
    width: 2px; height: 190px;
    background: linear-gradient(to bottom, rgba(26,98,176,.1), var(--brand-blue), rgba(26,98,176,.1));
  }
  .contact {
    position: absolute; left: 280px; top: 58px; right: 16px;
  }
  .contact__name {
    font-weight: 700; font-size: 23px; color: var(--brand-blue); line-height: 1.05;
  }
  .contact__title { font-size: 14px; margin-top: 2px; }
  .contact__address { font-style: normal; font-size: 14px; line-height: 1.3; margin-top: 10px; }
  .contact__list { list-style: none; margin-top: 8px; font-size: 13px; line-height: 1.4; }
  .contact__list li { display: flex; align-items: center; gap: 7px; }
  .contact__list svg { width: 11px; height: 11px; fill: var(--brand-blue); flex: none; }
  .contact__web-accent { color: var(--brand-blue); }
</style>
</head>
<body>
<main class="sheet">

  <section class="card card--front" aria-label="Business card front">
    <div class="front__badge" aria-hidden="true"></div>
    <div class="front__brand">
      <div class="brand-name">LIMBWORKS INC.</div>
      <div class="brand-tagline">Prosthetic &amp; Orthotic Services</div>
    </div>
    <ul class="services">
      <li class="service">
        <div class="service__icon" role="img" aria-label="Knee joint icon for orthotics"></div>
        <span class="service__label">ORTHOTICS</span>
      </li>
      <li class="service">
        <div class="service__icon" role="img" aria-label="Standing figure icon for prosthetics"></div>
        <span class="service__label">PROSTHETICS</span>
      </li>
      <li class="service">
        <div class="service__icon" role="img" aria-label="Wheelchair icon for vascular care"></div>
        <span class="service__label">VASCULAR</span>
      </li>
    </ul>
  </section>

  <section class="card card--back" aria-label="Business card back">
    <div class="back__badge">
      <span class="back__badge-name">LIMBWORKS<br>INC.</span>
    </div>
    <div class="back__divider" aria-hidden="true"></div>
    <div class="contact">
      <h1 class="contact__name">Mara Feldstein</h1>
      <p class="contact__title">Orthotist/Prosthetist</p>
      <address class="contact__address">2250 Harbor Ave.<br>Brooklyn, NY 11229</address>
      <ul class="contact__list">
        <li><svg viewBox="0 0 12 12" aria-hidden="true"><path d="M3 0h6a1 1 0 0 1 1 1v10a1 1 0 0 1-1 1H3a1 1 0 0 1-1-1V1a1 1 0 0 1 1-1zm0 2v7h6V2z"/></svg>555-0142-387</li>
        <li><svg viewBox="0 0 12 12" aria-hidden="true"><path d="M2.5 0.5l2 2.5-1.2 1.4a7 7 0 0 0 4.3 4.3L9 7.5l2.5 2-1.3 2A10 10 0 0 1 0.5 1.8z"/></svg>555.204.1700</li>
        <li><svg viewBox="0 0 12 12" aria-hidden="true"><path d="M3 0h5v3H3zM1 4h10v6H9v2H3v-2H1zm3 4v3h4V8z"/></svg>555.204.3919</li>
        <li><svg viewBox="0 0 12 12" aria-hidden="true"><path d="M0 2h12v8H0zm1 1v.4l5 3.2 5-3.2V3zm0 1.6V9h10V4.6L6 7.8z"/></svg>mfeldstein@limbworksinc.com</li>
        <li><svg viewBox="0 0 12 12" aria-hidden="true"><path d="M6 0a6 6 0 1 1 0 12A6 6 0 0 1 6 0zm0 1.2c-.8 1-1.3 2.6-1.3 4.8s.5 3.8 1.3 4.8c.8-1 1.3-2.6 1.3-4.8S6.8 2.2 6 1.2zM1.3 5.4h3V6.6h-3zm6.4 0h3V6.6h-3z"/></svg>www.<span class="contact__web-accent">limbworksinc</span>.com</li>
      </ul>
    </div>
  </section>

</main>
</body>
</html>
```